Classy, Elegant, Simple Business Card Design

Looking to have a classy, simple, and elegant design. Want a top notch designed business card. I really like the look of the new torvane credit card. I also like the design I attached. I am trying to reach 21-29 year old females for booking us for there wedding or event. We offer Disc Jockey Service, Photo Booth Rentals, and Uplighting .

Target Market(s)

21-28 year old females

Contact Information for Business Card

Has to have logo, website, email, and phone number

Font styles to use
Other font styles liked:
• open to font choice, modern, clean
Designer to choose
33a6d7
0791cd
0555a3
ffffff

Requirements
Must have
• Has to have logo, website, email, and phone number
Nice to have
• I really like the design of the new torvane credit card. I also included my logo and some designs I like
Should not have
• clutter or too much info

```html
<!DOCTYPE html>
<html lang="en">
<head>
<meta charset="utf-8">
<title>Bluecrest Event Group – Business Card</title>
<link rel="stylesheet" href="https://fonts.googleapis.com/css2?family=Poppins:wght@400;500&display=swap">
<style>
  :root {
    --backdrop: #1e1e1e;
    --card: #ffffff;
    --brand-blue: #0791cd;
    --deep-blue: #0555a3;
    --text-dark: #4a4a4a;
    --text-muted: #9a9a9a;
  }
  html, body {
    margin: 0;
    padding: 0;
    width: 1200px;
    height: 1200px;
    overflow: hidden;
    background: var(--backdrop);
    font-family: "Poppins", sans-serif;
  }
  .canvas {
    position: relative;
    width: 1200px;
    height: 1200px;
  }
  .card {
    position: absolute;
    left: 262px;
    width: 686px;
    height: 392px;
    background: var(--card);
  }
  .card--front { top: 165px; }
  .card--back { top: 653px; }

  .front-brand {
    position: absolute;
    right: 40px;
    top: 92px;
    margin: 0;
    font-size: 46px;
    font-weight: 500;
    letter-spacing: 1px;
    color: var(--deep-blue);
  }
  .holder {
    position: absolute;
    left: 35px;
    top: 240px;
  }
  .holder-name {
    margin: 0;
    font-size: 23px;
    font-weight: 500;
    line-height: 1.2;
    color: var(--brand-blue);
  }
  .holder-role {
    margin: 0;
    font-size: 15px;
    font-weight: 400;
    color: var(--text-muted);
  }
  .contact-list {
    list-style: none;
    margin: 22px 0 0;
    padding: 0;
  }
  .contact-item {
    display: flex;
    align-items: center;
    gap: 9px;
    font-size: 16px;
    line-height: 20px;
    color: var(--text-dark);
  }
  .contact-icon {
    width: 13px;
    height: 13px;
    flex: none;
  }

  .back-brand {
    position: absolute;
    left: 0;
    right: 0;
    top: 140px;
    margin: 0;
    text-align: center;
    font-size: 36px;
    font-weight: 500;
    letter-spacing: 1px;
    color: var(--deep-blue);
  }
  .services {
    position: absolute;
    left: 0;
    right: 0;
    top: 334px;
    margin: 0;
    text-align: center;
    font-size: 16px;
    color: var(--text-dark);
  }
  .services .dot {
    color: var(--brand-blue);
    margin: 0 3px;
  }
</style>
</head>
<body>
<main class="canvas">
  <section class="card card--front">
    <p class="front-brand">Bluecrest</p>
    <div class="holder">
      <h1 class="holder-name">Daniel Hartley</h1>
      <p class="holder-role">President</p>
      <ul class="contact-list">
        <li class="contact-item">
          <svg class="contact-icon" viewBox="0 0 16 16" aria-hidden="true"><path fill="#0791cd" d="M3.5 1.5l2.5 0 1 3.5-1.8 1.3c.9 1.9 2.4 3.4 4.3 4.3L10.8 8.8l3.5 1V12.3c0 1-.9 1.9-1.9 1.8C6.6 13.6 2.4 9.4 1.9 3.6 1.8 2.4 2.5 1.5 3.5 1.5z"/></svg>
          555-014-2287
        </li>
        <li class="contact-item">
          <svg class="contact-icon" viewBox="0 0 16 16" aria-hidden="true"><rect x="1" y="3.5" width="14" height="9" rx="1" fill="#0791cd"/><path d="M1.5 4.2L8 9l6.5-4.8" fill="none" stroke="#fff" stroke-width="1.2"/></svg>
          info@bluecrestevents.com
        </li>
        <li class="contact-item">
          <svg class="contact-icon" viewBox="0 0 16 16" aria-hidden="true"><circle cx="8" cy="8" r="6.8" fill="#0791cd"/><path d="M1.5 8h13M8 1.2c-2.6 3.6-2.6 10 0 13.6M8 1.2c2.6 3.6 2.6 10 0 13.6" fill="none" stroke="#fff" stroke-width="1"/></svg>
          www.bluecrestevents.com
        </li>
      </ul>
    </div>
  </section>

  <section class="card card--back">
    <p class="back-brand">Bluecrest Event Group</p>
    <p class="services">Disc Jockey Service<span class="dot">•</span>Photo Booth Rentals<span class="dot">•</span>Uplighting .</p>
  </section>
</main>
</body>
</html>
```